Quorimo Business Card Design Project

We need a business card design for quorimo.example a company based in Berlin, Germany.

?Quorimo is marketplace that enables people all over the world to monetize and exchange their individual knowledge and language skills through interactive video sessions. User are matched by their interests.

On Quorimo everybody can be student or teacher (seller or buyer).

We would love to see designs that use or main color blue and green. The design should communicate what Quorimo enables - see my notice above.

Looking so forward to your designs
Cheers from Berlin,
Lorenz

Target Market(s)

globally

Industry/Entity Type

Teacher

Requirements
Must have
• Lorenz Hubeck
CEO
Quorimo.example

Quorimo e-Services GmbH
Lindenweg 87
10247 Berlin

Fon: +49 30 418 906 25 17
Mobile: 49 172 54 91 37 6
E-Mail: l.hubeck@quorimo.example
Web: www.quorimo.example

```html
<!DOCTYPE html>
<html lang="en">
<head>
<meta charset="utf-8">
<title>Quorimo Business Card</title>
<link rel="stylesheet" href="https://fonts.googleapis.com/css2?family=Open+Sans:wght@400;600;700&display=swap">
<style>
  :root {
    --page: #e6e6e6;
    --card-top: #ffffff;
    --card-bottom: #e9e9ea;
    --blue: #1ea2dd;
    --green: #8dc63f;
    --grey: #6d6e70;
    --text: #58595b;
  }
  html, body {
    margin: 0;
    width: 954px;
    height: 1200px;
    overflow: hidden;
    background: var(--page);
    font-family: "Open Sans", Arial, sans-serif;
  }
  .card {
    position: absolute;
    left: 82px;
    width: 800px;
    height: 456px;
    border-radius: 26px;
    background: linear-gradient(180deg, var(--card-top) 0%, var(--card-bottom) 100%);
    box-shadow: 0 6px 14px rgba(0, 0, 0, 0.25);
    overflow: hidden;
  }
  .card--front { top: 89px; }
  .card--back { top: 654px; }
  .corner-swoosh {
    position: absolute;
    top: 0;
    left: 0;
    width: 800px;
    height: 456px;
  }
  .brand {
    position: absolute;
    left: 54px;
    top: 68px;
    height: 96px;
  }
  .brand__mark {
    position: absolute;
    left: 0;
    top: 0;
    width: 92px;
    height: 92px;
    background: var(--blue);
    border-radius: 6px;
  }
  .brand__name {
    position: absolute;
    left: 112px;
    top: -8px;
    margin: 0;
    font-size: 88px;
    font-weight: 400;
    color: var(--grey);
    letter-spacing: 1px;
    line-height: 1.1;
    white-space: nowrap;
  }
  .person {
    position: absolute;
    left: 54px;
    top: 255px;
  }
  .person__name {
    margin: 0;
    font-size: 30px;
    font-weight: 700;
    color: var(--blue);
    line-height: 1.1;
  }
  .person__role {
    margin: 2px 0 0;
    font-size: 18px;
    color: var(--text);
  }
  .company {
    position: absolute;
    left: 54px;
    top: 362px;
    margin: 0;
    font-size: 18px;
    line-height: 28px;
    color: var(--text);
    font-style: normal;
  }
  .contacts {
    position: absolute;
    left: 462px;
    top: 302px;
    margin: 0;
    padding: 0;
    list-style: none;
  }
  .contacts li {
    display: flex;
    align-items: center;
    height: 28.5px;
    font-size: 18px;
    color: var(--text);
  }
  .contacts svg {
    width: 22px;
    height: 20px;
    margin-right: 10px;
    fill: var(--grey);
  }
  .web {
    position: absolute;
    left: 59px;
    top: 374px;
    margin: 0;
    font-size: 22px;
    letter-spacing: 5px;
    color: var(--grey);
  }
  .web__accent { color: var(--blue); }
</style>
</head>
<body>

<section class="card card--front">
  <svg class="corner-swoosh" viewBox="0 0 800 456" aria-hidden="true">
    <path d="M535 0 Q752 45 800 308 V0 Z" fill="var(--green)"/>
    <path d="M552 0 Q760 44 800 285 V0 Z" fill="#ffffff"/>
    <path d="M572 0 Q768 42 800 268 V0 Z" fill="var(--blue)"/>
  </svg>
  <div class="brand">
    <span class="brand__mark"></span>
    <h1 class="brand__name">Quorimo</h1>
  </div>
  <div class="person">
    <h2 class="person__name">Lorenz Hubeck</h2>
    <p class="person__role">CEO</p>
  </div>
  <address class="company">Quorimo e-Services GmbH,<br>Lindenweg 87, 10247 Berlin</address>
  <ul class="contacts">
    <li>
      <svg viewBox="0 0 24 20" aria-hidden="true"><path d="M2 7c0-3 5-5 10-5s10 2 10 5l-4 1-1-2c-3-1-7-1-10 0L6 8z M6 10h12l3 8H3z"/></svg>
      +49 30 418 906 25 17
    </li>
    <li>
      <svg viewBox="0 0 24 20" aria-hidden="true"><path d="M8 0h2v3h4a2 2 0 0 1 2 2v13a2 2 0 0 1-2 2H10a2 2 0 0 1-2-2z M10 5v5h4V5z"/></svg>
      49 172 54 91 37 6
    </li>
    <li>
      <svg viewBox="0 0 24 20" aria-hidden="true"><path d="M2 4h20v14H2z M4 6v1l8 6 8-6V6z" fill-rule="evenodd"/></svg>
      l.hubeck@quorimo.example
    </li>
    <li>
      <svg viewBox="0 0 24 20" aria-hidden="true"><circle cx="12" cy="10" r="9"/><path d="M5 6h5l2 3-3 3H6z M14 4h4l1 4-3 2z M13 13h5l-3 5z" fill="#ffffff"/></svg>
      www.quorimo.example
    </li>
  </ul>
</section>

<section class="card card--back">
  <svg class="corner-swoosh" viewBox="0 0 800 456" aria-hidden="true">
    <path d="M535 0 Q752 45 800 308 V0 Z" fill="var(--green)"/>
    <path d="M552 0 Q760 44 800 285 V0 Z" fill="#ffffff"/>
    <path d="M572 0 Q768 42 800 268 V0 Z" fill="var(--blue)"/>
  </svg>
  <div class="brand">
    <span class="brand__mark"></span>
    <h2 class="brand__name">Quorimo</h2>
  </div>
  <p class="web">www.<span class="web__accent">quorimo</span>.example</p>
</section>

</body>
</html>
```